Kestrel Home Business Card Design

We need a business card for a Building company based in Queensland, Australia. Our colours are orange black and we do base all our homes design names and other aspect of our business on astrology. We want the consumer to perceive the company as professional and to attract investors to our company.We have over 20 years in the building industry.We pride ourselves on our innovation of designs and making the building process for anyone from families to investor a smooth and simple experience.
Business
Amelia Prichard0411752116PO Box 454, Mudgeerbaameliaprichard@zodiachomes.com

```html
<!DOCTYPE html>
<html lang="en">
<head>
<meta charset="utf-8">
<title>Kestrel Homes Business Card</title>
<link href="https://fonts.googleapis.com/css2?family=Archivo:wght@400;700;800&display=swap" rel="stylesheet">
<style>
  :root {
    --backdrop: #e6e6e6;
    --card-white: #f7f7f7;
    --brand-orange: #ee9229;
    --ink: #1c1c1c;
    --paper-white: #ffffff;
  }
  * { margin: 0; padding: 0; box-sizing: border-box; }
  html, body {
    width: 1200px;
    height: 900px;
    overflow: hidden;
    background: var(--backdrop);
    font-family: "Archivo", Arial, sans-serif;
  }
  .canvas {
    position: relative;
    width: 1200px;
    height: 900px;
    display: flex;
    align-items: center;
    justify-content: center;
    gap: 60px;
  }
  .card {
    position: relative;
    width: 500px;
    height: 286px;
    box-shadow: 0 6px 18px rgba(0,0,0,0.12);
  }
  .card--details {
    background: var(--card-white);
    color: var(--ink);
  }
  .card--brand {
    background: var(--brand-orange);
    display: flex;
    align-items: center;
    justify-content: center;
  }
  .contact {
    position: absolute;
    left: 34px;
    top: 30px;
  }
  .contact__name {
    color: var(--brand-orange);
    font-weight: 700;
    font-size: 19px;
    line-height: 1.1;
  }
  .contact__role {
    font-size: 12px;
    margin-bottom: 18px;
  }
  .contact__label {
    color: var(--brand-orange);
    font-size: 12px;
    line-height: 1.2;
  }
  .contact__value {
    font-size: 13px;
    line-height: 1.25;
  }
  .wordmark {
    display: flex;
    flex-direction: column;
    align-items: flex-end;
    font-weight: 800;
    white-space: nowrap;
    line-height: 1;
  }
  .wordmark__dot {
    flex: none;
    display: block;
    margin-bottom: 6px;
  }
  .card--details .wordmark {
    position: absolute;
    right: 34px;
    bottom: 36px;
    font-size: 27px;
    color: var(--ink);
  }
  .card--details .wordmark__dot { margin-right: 42px; }
  .card--brand .wordmark {
    font-size: 34px;
    color: var(--paper-white);
    margin-top: 10px;
  }
  .card--brand .wordmark__dot { margin-right: 52px; }
</style>
</head>
<body>
  <main class="canvas">
    <section class="card card--details" aria-label="Business card back">
      <div class="contact">
        <p class="contact__name">Harriet Colvane</p>
        <p class="contact__role">Managing Director</p>
        <p class="contact__label">telephone</p>
        <p class="contact__value">0491 570 156</p>
        <p class="contact__label">email</p>
        <p class="contact__value">harrietcolvane@kestrelhomes.example</p>
        <p class="contact__label">address</p>
        <p class="contact__value">PO Box 872, Queensland</p>
      </div>
      <div class="wordmark">
        <svg class="wordmark__dot" width="40" height="40" viewBox="0 0 40 40" aria-hidden="true">
          <circle cx="20" cy="20" r="19" fill="var(--brand-orange)"/>
        </svg>
        <span>Kestrel Homes</span>
      </div>
    </section>

    <section class="card card--brand" aria-label="Business card front">
      <div class="wordmark">
        <svg class="wordmark__dot" width="48" height="48" viewBox="0 0 48 48" aria-hidden="true">
          <circle cx="24" cy="24" r="23" fill="var(--ink)"/>
        </svg>
        <span>Kestrel Homes</span>
      </div>
    </section>
  </main>
</body>
</html>
```